Ten-Harvest Brochure

We would like a 3 panel layout format with copy on both sides and on each panel, (we will provide content).

We are Ten-Harvest and we work with business owners to achieve measurable growth and success based on 5 Core Pillars Of Momentum and (S.L.K) 60 Week Progress Roadmap Scheme. We also work with the business leader and individuals within the organization with personal development.

We would like the brochure to have a corporate feel, but warm and inviting. We don't want a hard or aggressive feel.

We would like it to be available for pdf upload and physical print formats.

The winning design will also be invited to design a header for our website as well. The header will be consistent with the brochure, so please keep that in mind during your creative process.

I am enclosing a transparent copy of our company logo along with content for the brochure.

Thank you in advance for your consideration!

Gareth and Moira
Updates

Sorry, but we forgot to include the front cover text.

It will read as follows,

Do you know the 5 Core Pillars Of Momentum  that are crucial to the success of any business today?

Also, please add the following to the back page

Website: www.ten-harvest.example
Resource Centre: www.thresourcehub.example 
Phone: +44 (0) 7612583047
Email: info@ten-harvest.example

Follow us on (please insert Facebook, Linkedin and YouTube logo)

I have uploaded a pdf format of brochure text.

Hello designers. I wanted to give some further input to help the process. Although the brochure is to target business, we don't want to over do it with corporate professioanls in all the photos. If there is an opportunity to incorporate photos of small business owners like, a butcher, baker, chef, flower shop etc. This would hopefully help us make an immpression to all small business owners.

Thank you, and good luck!

Gareth and Moira  

Reason: A few designers have come come on board last minute. So I'd like to give everyone the same opportunity to respond. Sincerely, Gareth

Target Market(s)

Small Business Owners searching for new ways to grow their business in the UK and Republic Of Ireland.

Industry/Entity Type

Business

```html
<!DOCTYPE html>
<html lang="en">
<head>
<meta charset="utf-8">
<title>Ten-Harvest Brochure – Inside Spread</title>
<link rel="stylesheet" href="https://fonts.googleapis.com/css2?family=Archivo+Black&family=Didact+Gothic&family=Arimo:wght@400;700&display=swap">
<style>
  :root {
    --navy: #1b1c3a;
    --purple: #8e3a8c;
    --grey: #8b8b94;
    --white: #ffffff;
    --paper-bg: #e9e9ea;
    --rule: #4a4b66;
    --photo-light: #f4f7fb;
    --photo-blue: #bcd3ec;
  }
  * { box-sizing: border-box; margin: 0; padding: 0; }
  html, body {
    width: 1200px; height: 1000px; overflow: hidden;
    background: var(--paper-bg);
  }
  .spread {
    position: absolute; left: 105px; top: 150px;
    width: 990px; height: 700px;
    display: flex;
    box-shadow: 0 18px 40px rgba(0,0,0,.18);
  }
  .panel {
    width: 330px; height: 700px;
    position: relative;
    font-family: "Didact Gothic", "Century Gothic", sans-serif;
    color: var(--white);
  }
  .panel--dark { background: var(--navy); padding: 30px 30px; }
  .panel--photo {
    background: linear-gradient(160deg, var(--photo-light) 0%, #dfe8f3 45%, var(--photo-blue) 100%);
  }
  .heading {
    font-family: "Archivo Black", "Arial Black", sans-serif;
    font-size: 27px; line-height: 1; letter-spacing: 1.5px;
    text-transform: uppercase;
  }
  .heading__top { color: var(--grey); display: block; }
  .heading__bottom { color: var(--purple); display: block; }
  .heading-row { display: flex; align-items: center; gap: 12px; margin-bottom: 14px; }
  .icon { width: 52px; height: 52px; flex: none; }

  .intro { text-align: center; font-size: 13px; line-height: 1.35; }
  .intro__link { font-family: "Arimo", Arial, sans-serif; font-weight: 700; font-size: 16px; margin: 2px 0; }
  .intro__phone { font-family: "Arimo", Arial, sans-serif; font-weight: 700; font-size: 20px; letter-spacing: 2px; margin: 2px 0; }
  .intro__offer { font-family: "Arimo", Arial, sans-serif; font-weight: 700; font-size: 20px; margin: 2px 0 4px; }
  .body-text { font-size: 13px; line-height: 1.4; text-align: justify; }
  .body-text strong { font-family: "Arimo", Arial, sans-serif; font-weight: 700; }
  .section-gap { margin-top: 26px; }

  .pillars { list-style: none; margin: 10px 0 12px 24px; font-family: "Arimo", Arial, sans-serif; font-weight: 700; font-size: 13px; line-height: 1.85; }
  .pillars li::before { content: "- "; }

  .services { list-style: none; margin-top: 12px; font-family: "Arimo", Arial, sans-serif; font-weight: 700; font-size: 12.5px; line-height: 1.75; }
  .divider { border: 0; border-top: 1px solid var(--rule); margin: 22px 0 26px; }
  .link-accent { color: var(--purple); }

  .brand {
    position: absolute; right: 30px; bottom: 28px;
    display: flex; align-items: center; gap: 8px;
    font-family: "Archivo Black", "Arial Black", sans-serif;
    font-size: 14px; letter-spacing: 1px; color: var(--grey);
    text-transform: uppercase;
  }
  .brand__mark { width: 14px; height: 14px; background: var(--purple); }
</style>
</head>
<body>
<main class="spread">

  <section class="panel panel--dark panel--left">
    <div class="heading-row">
      <svg class="icon" viewBox="0 0 52 52" aria-hidden="true">
        <circle cx="26" cy="15" r="7" fill="#8b8b94"/>
        <path d="M14 44 V30 a12 10 0 0 1 24 0 V44 Z" fill="#8b8b94"/>
        <path d="M4 4 L12 4 M4 4 L4 12 M4 4 L13 13 M48 4 L40 4 M48 4 L48 12 M48 4 L39 13 M4 48 L12 48 M4 48 L4 40 M4 48 L13 39 M48 48 L40 48 M48 48 L48 40 M48 48 L39 39" stroke="#8e3a8c" stroke-width="3" fill="none"/>
      </svg>
      <h2 class="heading"><span class="heading__top">Getting</span><span class="heading__bottom">Started</span></h2>
    </div>
    <div class="intro">
      <p>The first step is to visit</p>
      <p class="intro__link">www.ten-harvest.example</p>
      <p>or call</p>
      <p class="intro__phone">07612583047</p>
      <p>to book your</p>
      <p class="intro__offer">FREE CONSULTATION.</p>
    </div>
    <p class="body-text">This will be an opportunity for you to think about where you want your business to go and for us to establish how we can help you get there.</p>

    <div class="heading-row section-gap">
      <svg class="icon" viewBox="0 0 52 52" aria-hidden="true">
        <circle cx="24" cy="22" r="7" fill="#8b8b94"/>
        <path d="M10 48 V38 a14 10 0 0 1 28 0 V48 Z" fill="#8b8b94"/>
        <circle cx="36" cy="10" r="9" fill="#8e3a8c"/>
        <text x="36" y="15" text-anchor="middle" font-family="Arimo, sans-serif" font-weight="700" font-size="13" fill="#1b1c3a">?</text>
      </svg>
      <h2 class="heading"><span class="heading__top">After</span><span class="heading__bottom">That?</span></h2>
    </div>
    <p class="body-text">We will carry out a business analysis based on <strong>The 5 Core Pillars Of Momentum:</strong></p>
    <ul class="pillars">
      <li>Your Brand</li>
      <li>Sales</li>
      <li>Your People</li>
      <li>Product and Service</li>
      <li>Psychology and Skills</li>
      <li>Finance</li>
    </ul>
    <p class="body-text">We then provide you with a detailed report and work with you to create and implement your Progress Roadmap Scheme (S.L.K.). This is a 60 week plan, customized for your business and designed so you can start seeing positive and measurable results immediately.</p>
  </section>

  <section class="panel panel--photo" role="img" aria-label="Photo of two business people shaking hands over a desk covered with printed charts and reports"></section>

  <section class="panel panel--dark panel--right">
    <h2 class="heading"><span class="heading__top">Business</span><span class="heading__bottom">Solutions</span></h2>
    <p class="body-text" style="margin-top:14px">In addition to the Total Business Analysis / S.L.K package, we also offer other business solutions which can be used individually or bundled together to create a package suitable for your needs.</p>
    <ul class="services">
      <li>One on one business mentoring</li>
      <li>Marketing strategies</li>
      <li>Sales training (individual or group)</li>
      <li>Management training (individual or group)</li>
      <li>Customer service training (individual or group)</li>
    </ul>
    <hr class="divider">
    <h2 class="heading"><span class="heading__top">Resource</span><span class="heading__bottom">Centre</span></h2>
    <p class="body-text" style="margin-top:14px">At Ten-Harvest, we are dedicated to providing current and relevant information through our resource centre <span class="link-accent">www.thresourcehub.example</span> where you will find access to videos, reports, statistics and newsletters. You will also find details on upcoming events, such as webinars, workshops and online training.</p>
    <div class="brand"><span class="brand__mark"></span>Ten-Harvest</div>
  </section>

</main>
</body>
</html>
```